Luxury Tours Design

We are “Amber Coachline” a Chauffeur Company based in Maidenhead, Berkshire. Our website is - ambercoachline.co.uk which will give you an insite into the Company.
Our clients consist of luxurious Hotels, large Corporate Companies along with private UHNW clients.
We have a fleet of Valtrane E, S and V Class vehicles along with 16 Seater Executive Coaches so we can accommodate single travellers, couples, friends, families and groups.
We would like an A5 (or slightly larger) double sided colour leaflet designed to promote our Tours in our local and surrounding areas.
The information below is some indication as to what we would like.
On the front we would like:-
Amber Coachline “Signature Tour” This will be our main promoting Tour
Slogan “Amber Coachline….ever at your service”
Tour will include:-
Visiting the historic town of Windsor, Hollenby Castle, St Aldric’s Chapel and Regal Pemberly Shopping Arcade.
Then onto Eton (Dunmere College) and a lovely view of the River Thames along with an array of Antique Shops in the quaint streets.
Bray Village (Heron Isle), renowed for it’s Brevard Star Restaurants and pubs.
Through picturesque Cookham along to Marlow for some shopping in the boutique shops, small listed buildings and beautiful places for refreshments, along with stunning views of the River Thames form Ashcombe Bridge.
This will be our main tour we offer but again this is flexible. This aims to be around 4-5 hours.
On the front, a picture of Hollenby castle maybe a large picture with writing over the top, or a separate photo….. a couple of photos attached or something similar.
On the back of the leaflet:-
We offer London based tours including:-
Belvards, Larkmoor Park, Ravensholt Palace, Corringdale Palace, Pellington Square, Turning of the Sentries, Keep of Ardmoor, Tall Tom, Glenmoreton Abbey to name a few! Or maybe London by night with a show or restaurant.
On the back a picture of Corringdale Palace…a couple of picture are also attached or again something similar.
Other Tours provided:-
Ridgewell Court Palace, Oxford and Corvane Palace, Ashmarrow Ring and Bath, The Cotswolds, Stratford and Penlow Castle, Quillford Shopping Village.
Also bespoke Tours can be arranged. We can personalise any tour to your requirements.
Experienced friendly Chauffeur’s, no request too big or small.
Please call us on 01632 960417 or email us sales@ambercoachline.co.uk
Please can you do an initial design including the above information.
Look forward to hearing from you.
Kind regards
Please visit https://www.hartleyprivatedrives.co.uk/ to get an idea of the tours of London to go on the back.
Prices will follow to be added after design and layout has been done.
Our AC logo is available on www.ambercoachline.co.uk
We want text to be editable and also for the design to have a luxury feel.
Chauffeur

```html
<!DOCTYPE html>
<html lang="en">
<head>
<meta charset="utf-8">
<title>Amber Coachline – Tours Leaflet</title>
<link rel="stylesheet" href="https://fonts.googleapis.com/css2?family=Great+Vibes&family=Poppins:ital,wght@0,300;0,400;0,500;0,600;1,400;1,600&display=swap">
<style>
:root{
  --stage:#777777;
  --ink-dark:#2b2924;
  --olive:#5a5030;
  --panel:rgba(120,108,70,.78);
  --price:#9c8b45;
  --gold:#d6c164;
  --gold-soft:#e3cf6e;
  --white:#ffffff;
  --text-dark:#222222;
}
*{margin:0;padding:0;box-sizing:border-box}
html,body{width:1200px;height:2400px;overflow:hidden;background:var(--stage)}
.stage{position:absolute;left:0;top:0;width:1288px;height:2576px;transform:scale(.9317);transform-origin:0 0;font-family:"Poppins",sans-serif}
.leaflet{position:absolute;left:265px;width:757px;height:1075px;background:var(--ink-dark);overflow:hidden}
.leaflet--front{top:131px}
.leaflet--back{top:1288px}
.photo{position:absolute;left:0;width:100%}
.front-photo{top:0;height:620px;background:linear-gradient(180deg,#c9d8e3 0%,#e9c9c0 24%,#f1a596 32%,#8a8a78 40%,#4f7a35 52%,#3f6a2c 70%,#4d5a3a 84%,var(--ink-dark) 100%)}
.back-photo{top:0;height:700px;background:linear-gradient(180deg,#dfe3e8 0%,#e8dcd8 22%,#eeb9a8 32%,#d9d6d0 42%,#c8c6c0 60%,#d9a232 70%,#c63a2a 80%,#6b6a3a 92%,var(--ink-dark) 100%)}
.script{position:absolute;left:0;width:100%;text-align:center;font-family:"Great Vibes",cursive;font-weight:400}
.front-title{top:28px;font-size:96px;color:var(--olive)}
.front-slogan{top:136px;font-size:42px;color:var(--olive)}
.fleet-note{position:absolute;left:40px;right:40px;top:480px;text-align:center;color:var(--white);font-size:18.5px;font-weight:500;line-height:22px}
.tour-panel{position:absolute;left:89px;top:592px;width:580px;height:326px;background:var(--panel)}
.tour-heading{position:absolute;left:22px;top:10px;color:var(--gold);font-size:25px;font-weight:500;line-height:25px;text-transform:uppercase}
.price-tag{position:absolute;left:391px;top:6px;width:189px;height:52px;background:var(--price);color:var(--white);padding:4px 0 0 30px}
.price-amount{font-size:28px;font-weight:600;line-height:30px}
.price-amount sup{font-size:15px;vertical-align:10px}
.price-note{font-size:11.5px;line-height:13px}
.tour-stops{position:absolute;left:22px;top:80px;width:530px;color:var(--white);font-size:12.6px;line-height:15px}
.tour-stops p{margin-bottom:15px}
.pull-quote{position:absolute;left:0;width:100%;text-align:center;color:var(--gold-soft);font-style:italic}
.tour-panel .pull-quote{top:276px;font-size:16.5px}
.pull-quote .mark{font-family:Georgia,serif;font-style:normal;font-weight:700;font-size:28px;vertical-align:-4px;color:var(--gold)}
.contact-label{position:absolute;left:0;width:100%;text-align:center;color:var(--gold);font-size:11.5px;letter-spacing:2px;font-weight:500}
.contact-row{position:absolute;left:96px;right:40px;display:flex;align-items:center;color:var(--white);font-weight:600}
.contact-item{display:flex;align-items:center;gap:7px}
.contact-item svg{width:14px;height:14px}
.contact-phone{font-size:14.5px}
.contact-mail,.contact-web{font-size:12px}
.divider{width:1px;height:14px;background:#8c8670;margin:0 22px}
.brand{position:absolute;left:0;width:100%;display:flex;justify-content:center;align-items:center;gap:10px;color:#e4e0d6;font-size:31px;font-weight:300}
.brand-dot{width:30px;height:30px;border-radius:50%;background:#8e876c}
.back-title{top:22px;font-size:84px;color:var(--text-dark)}
.sights{position:absolute;top:120px;color:var(--text-dark);font-size:16px;line-height:29px;list-style:none}
.sights--a{left:69px}.sights--b{left:273px}.sights--c{left:529px;top:116px}
.night-line{position:absolute;left:68px;top:226px;font-size:15.5px;font-weight:600;font-style:italic;color:var(--text-dark)}
.other-panel{position:absolute;left:81px;top:635px;width:611px;height:298px;background:var(--panel)}
.other-title{top:12px;font-size:54px;color:var(--gold)}
.other-list{position:absolute;top:102px;list-style:none;color:var(--white);font-size:14px;line-height:29px;text-transform:uppercase}
.other-list--a{left:58px}.other-list--b{left:339px}
.other-panel .pull-quote{top:210px;font-size:15px;line-height:18px;padding:0 30px}
</style>
</head>
<body>
<div class="stage">

  <section class="leaflet leaflet--front">
    <div class="photo front-photo" role="img" aria-label="Photograph of Hollenby Castle at sunset seen down a long tree-lined avenue"></div>
    <h1 class="script front-title">Signature Tour</h1>
    <p class="script front-slogan">Amber Coachline….ever at your service</p>
    <p class="fleet-note">We have a fleet of Valtrane E, S and V Class vehicles along with 16 Seater Executive Coaches so we can accommodate single travellers, couples, friends, families and groups.</p>

    <div class="tour-panel">
      <h2 class="tour-heading">Visit to the historic<br>town of Windsor</h2>
      <div class="price-tag">
        <div class="price-amount"><sup>$</sup>8599<sup>.00</sup></div>
        <div class="price-note">(INCLUSIVE ALL TAXES)</div>
      </div>
      <div class="tour-stops">
        <p>Visiting the historic town of Windsor, Hollenby Castle, St Aldric’s Chapel and Regal Pemberly Shopping Arcade.</p>
        <p>Eton and Dunmere College with lovely views of the River Thames along with an array of Antique Shops in the quaint streets.</p>
        <p>Bray Village renowned for it's Brevard Star restaurants and pubs, along with a visit to Heron Isle.</p>
        <p>Through picturesque Cookham along to Marlow for some shopping in the boutique shops, small listed buildings and beautiful places for refreshments, along with stunning views of the River Thames from Ashcombe Bridge.</p>
      </div>
      <p class="pull-quote"><span class="mark">“</span>Our signature tour is approximately 4 hours<span class="mark">”</span></p>
    </div>

    <p class="contact-label" style="top:934px">CONTACT US</p>
    <div class="contact-row" style="top:957px">
      <span class="contact-item contact-phone"><svg viewBox="0 0 16 16"><circle cx="8" cy="8" r="7" fill="none" stroke="#d6c164" stroke-width="1"/><path d="M5.5 4.5l1.5 0 .7 2-1 .8a5 5 0 0 0 2 2l.8-1 2 .7v1.5a1 1 0 0 1-1 1A6 6 0 0 1 4.5 5.5a1 1 0 0 1 1-1z" fill="#d6c164"/></svg>01632 960417</span>
      <span class="divider"></span>
      <span class="contact-item contact-mail"><svg viewBox="0 0 16 16"><circle cx="8" cy="8" r="7" fill="none" stroke="#d6c164" stroke-width="1"/><rect x="4.5" y="5.5" width="7" height="5" fill="none" stroke="#d6c164" stroke-width="1"/><path d="M4.5 5.5l3.5 3 3.5-3" fill="none" stroke="#d6c164" stroke-width="1"/></svg>sales@ambercoachline.co.uk</span>
      <span class="divider"></span>
      <span class="contact-item contact-web"><svg viewBox="0 0 16 16"><circle cx="8" cy="8" r="7" fill="none" stroke="#d6c164" stroke-width="1"/><circle cx="8" cy="8" r="4" fill="none" stroke="#d6c164" stroke-width="1"/><path d="M4 8h8M8 4v8" stroke="#d6c164" stroke-width="1"/></svg>www.ambercoachline.co.uk</span>
    </div>
    <div class="brand" style="top:1000px"><span class="brand-dot"></span>Amber Coachline</div>
  </section>

  <section class="leaflet leaflet--back">
    <div class="photo back-photo" role="img" aria-label="Photograph of Corringdale Palace and its memorial behind beds of red and yellow tulips"></div>
    <h1 class="script back-title">London Tours</h1>
    <ul class="sights sights--a"><li>Belvards</li><li>Larkmoor Park</li><li>Ravensholt Palace</li></ul>
    <ul class="sights sights--b"><li>Corringdale Palace</li><li>Pellington Square</li><li>Turning of the Sentries</li></ul>
    <ul class="sights sights--c"><li>Keep of Ardmoor</li><li>Tall Tom</li><li>Glenmoreton Abbey</li></ul>
    <p class="night-line">Or maybe London by night with a show or restaurant.</p>

    <div class="other-panel">
      <h2 class="script other-title">Other Tours Provided</h2>
      <ul class="other-list other-list--a"><li>Ridgewell Court Palace</li><li>Oxford and Corvane Palace</li><li>Ashmarrow Ring and Bath</li></ul>
      <ul class="other-list other-list--b"><li>The Cotswolds</li><li>Stratford and Penlow Castle</li><li>Quillford Shopping Village</li></ul>
      <p class="pull-quote"><span class="mark">“</span>Also bespoke tours can be arranged. We can personalize any tour to your requirements with our friendly, experienced chauffeurs<span class="mark">”</span></p>
    </div>

    <p class="contact-label" style="top:955px">CONTACT US</p>
    <div class="contact-row" style="top:977px">
      <span class="contact-item contact-phone"><svg viewBox="0 0 16 16"><circle cx="8" cy="8" r="7" fill="none" stroke="#d6c164" stroke-width="1"/><path d="M5.5 4.5l1.5 0 .7 2-1 .8a5 5 0 0 0 2 2l.8-1 2 .7v1.5a1 1 0 0 1-1 1A6 6 0 0 1 4.5 5.5a1 1 0 0 1 1-1z" fill="#d6c164"/></svg>01632 960417</span>
      <span class="divider"></span>
      <span class="contact-item contact-mail"><svg viewBox="0 0 16 16"><circle cx="8" cy="8" r="7" fill="none" stroke="#d6c164" stroke-width="1"/><rect x="4.5" y="5.5" width="7" height="5" fill="none" stroke="#d6c164" stroke-width="1"/><path d="M4.5 5.5l3.5 3 3.5-3" fill="none" stroke="#d6c164" stroke-width="1"/></svg>sales@ambercoachline.co.uk</span>
      <span class="divider"></span>
      <span class="contact-item contact-web"><svg viewBox="0 0 16 16"><circle cx="8" cy="8" r="7" fill="none" stroke="#d6c164" stroke-width="1"/><circle cx="8" cy="8" r="4" fill="none" stroke="#d6c164" stroke-width="1"/><path d="M4 8h8M8 4v8" stroke="#d6c164" stroke-width="1"/></svg>www.ambercoachline.co.uk</span>
    </div>
    <div class="brand" style="top:1003px"><span class="brand-dot"></span>Amber Coachline</div>
  </section>

</div>
</body>
</html>
```